Veldmark Supplies Business Card

Professional business card that stand out to our potential customers. Front and back with clean modern design

Industry/Entity Type

Oil and gas

Contact Information for Business Card

Name, address, website , office phone and cell number

Requirements
Must have
• Editable files for each employee

```html
<!DOCTYPE html>
<html lang="en">
<head>
<meta charset="utf-8">
<title>Veldmark Supplies Business Card</title>
<link rel="stylesheet" href="https://fonts.googleapis.com/css2?family=Arimo:wght@400;700&family=Archivo+Black&display=swap">
<style>
  :root {
    --stage: #3d3d3d;
    --brand-red: #ff0000;
    --brand-blue: #00acd1;
    --paper: #ffffff;
    --ink-light: #ffffff;
  }
  * { margin: 0; padding: 0; box-sizing: border-box; }
  html, body {
    width: 1200px; height: 803px; overflow: hidden;
    background: var(--stage);
    font-family: "Arimo", Arial, sans-serif;
  }
  .canvas {
    position: relative; width: 1200px; height: 803px;
    display: flex; align-items: center; justify-content: center; gap: 60px;
  }
  .card {
    position: relative; width: 520px; height: 298px;
    border-radius: 22px; overflow: hidden;
    box-shadow: 0 18px 40px rgba(0,0,0,0.45);
  }
  .card--front { background: var(--brand-red); color: var(--ink-light); }
  .card--back { background: var(--paper); border-bottom: 4px solid var(--brand-blue); }

  .brand-name {
    font-family: "Archivo Black", Arial, sans-serif;
    text-transform: uppercase; letter-spacing: 0.5px; white-space: nowrap;
    display: flex; align-items: center; gap: 8px;
  }
  .brand-name__square { display: inline-block; }

  .front-mark {
    position: absolute; right: 36px; top: 40px; width: 200px;
    font-size: 26px; line-height: 1.15; color: var(--ink-light);
    flex-direction: column; align-items: flex-start; white-space: normal;
  }
  .front-mark .brand-name__square {
    width: 40px; height: 40px; background: var(--brand-blue); margin-bottom: 8px;
  }

  .front-info { position: absolute; left: 32px; bottom: 28px; width: 260px; }
  .front-info .brand-name { font-size: 15px; color: var(--ink-light); margin-bottom: 14px; }
  .front-info .brand-name__square { width: 12px; height: 12px; background: var(--brand-blue); }
  .person-name { font-size: 22px; font-weight: 700; color: var(--brand-blue); line-height: 1.05; }
  .person-role { font-size: 11px; margin-bottom: 10px; }
  .address { font-size: 11.5px; line-height: 1.35; margin-bottom: 8px; }
  .contact-list { list-style: none; font-size: 11.5px; line-height: 1.45; }
  .contact-list li { display: flex; align-items: center; gap: 6px; }
  .contact-list svg { width: 11px; height: 11px; flex: none; }

  .back-mark {
    position: absolute; left: 50%; top: 50%; transform: translate(-50%, -50%);
    font-size: 28px; color: var(--brand-red);
  }
  .back-mark .brand-name__square { width: 26px; height: 26px; background: var(--brand-blue); }
</style>
</head>
<body>
<main class="canvas">
  <section class="card card--front" aria-label="Business card front">
    <div class="brand-name front-mark">
      <span class="brand-name__square"></span>
      <span>Veldmark Supplies</span>
    </div>
    <div class="front-info">
      <div class="brand-name"><span class="brand-name__square"></span><span>Veldmark Supplies</span></div>
      <p class="person-name">Aaron Dekker</p>
      <p class="person-role">President</p>
      <p class="address">4120 Harlow Ridge Road<br>Brookfield, Canada 58210</p>
      <ul class="contact-list">
        <li>
          <svg viewBox="0 0 12 12" fill="var(--brand-blue)"><path d="M2.5 1 L4.5 1 L5 3.5 L3.8 4.5 Q5 7 7.5 8.2 L8.5 7 L11 7.5 L11 9.5 Q10.5 11 9 11 Q1 10 1 3 Q1 1.5 2.5 1Z"/></svg>
          <span>555-210-4187</span>
        </li>
        <li>
          <svg viewBox="0 0 12 12" fill="none" stroke="var(--brand-blue)" stroke-width="1.4"><rect x="3" y="1" width="6" height="10" rx="1"/><line x1="5" y1="9.3" x2="7" y2="9.3"/></svg>
          <span>555-382-9046</span>
        </li>
        <li>
          <svg viewBox="0 0 12 12"><rect x="1" y="2.5" width="10" height="7" fill="var(--brand-blue)"/><path d="M1 2.5 L6 6.5 L11 2.5" fill="none" stroke="var(--brand-red)" stroke-width="1"/></svg>
          <span>info@veldmarksupplies.com</span>
        </li>
        <li>
          <svg viewBox="0 0 12 12" fill="none" stroke="var(--brand-blue)" stroke-width="1.2"><circle cx="6" cy="6" r="5"/><ellipse cx="6" cy="6" rx="2.2" ry="5"/><line x1="1" y1="6" x2="11" y2="6"/></svg>
          <span>www.veldmarksupplies.com</span>
        </li>
      </ul>
    </div>
  </section>

  <section class="card card--back" aria-label="Business card back">
    <div class="brand-name back-mark">
      <span class="brand-name__square"></span>
      <span>Veldmark Supplies</span>
    </div>
  </section>
</main>
</body>
</html>
```